Redesign of business card for Cedar Ridge Mechanical

We are looking for a new design for our business cards for Cedar Ridge Mechanical. We are a plumbing & HVAC construction company, operating on the West Coast of Canada and USA. Logo attached.
Industry/Entity Type
Construction - Plumbing & HVAC
Contact Information for Business Card
Name, address, phone numbers, email, website address
Look and feel
Each slider illustrates characteristics of the customer's brand and the style your logo design should communicate.

```html
<!DOCTYPE html>
<html lang="en">
<head>
<meta charset="UTF-8">
<title>Cedar Ridge Mechanical – Business Card</title>
<link href="https://fonts.googleapis.com/css2?family=Montserrat:wght@400;700&display=swap" rel="stylesheet">
<style>
  :root {
    --backdrop: #222222;
    --card: #ffffff;
    --ink: #111111;
    --ink-soft: #333333;
  }
  * { box-sizing: border-box; margin: 0; padding: 0; }
  html, body {
    width: 1200px; height: 780px; overflow: hidden;
    background: var(--backdrop);
    font-family: "Montserrat", sans-serif;
    color: var(--ink);
  }
  .sheet {
    width: 1200px; height: 780px;
    display: flex; align-items: center; justify-content: center; gap: 40px;
  }
  .card {
    width: 540px; height: 310px;
    background: var(--card);
    position: relative; overflow: hidden;
  }

  /* Back: contact side */
  .card-back .brand-mark {
    position: absolute; left: 28px; top: 26px;
    font-weight: 700; font-size: 30px; line-height: 1.1;
    text-transform: uppercase; letter-spacing: 1px; width: 240px;
  }
  .card-back .address {
    position: absolute; left: 28px; bottom: 30px;
    font-size: 12px; line-height: 1.5; color: var(--ink-soft);
  }
  .card-back .company {
    position: absolute; right: 42px; top: 28px;
    display: flex; align-items: center; gap: 8px;
    font-weight: 700; font-size: 13px; text-transform: uppercase; letter-spacing: 1px;
  }
  .company .square { width: 12px; height: 12px; background: var(--ink); }
  .card-back .person {
    position: absolute; right: 42px; top: 110px; text-align: right;
  }
  .person .name { font-weight: 700; font-size: 20px; letter-spacing: 1px; text-transform: uppercase; }
  .person .role { font-size: 13px; color: var(--ink-soft); margin-top: 2px; }
  .card-back .contacts {
    position: absolute; right: 42px; bottom: 26px;
    list-style: none; text-align: right; font-size: 13px; line-height: 1.75;
  }
  .contacts li { display: flex; align-items: center; justify-content: flex-end; gap: 8px; }
  .contacts svg { width: 12px; height: 12px; fill: var(--ink); }
  .card-back .edge-strip {
    position: absolute; right: 0; top: 210px; width: 14px; height: 100px; background: var(--ink);
  }

  /* Front: brand side */
  .card-front { display: flex; align-items: center; justify-content: center; }
  .card-front .company {
    display: flex; align-items: center; gap: 14px;
    font-weight: 700; font-size: 28px; text-transform: uppercase; letter-spacing: 1px;
  }
  .card-front .square { width: 26px; height: 26px; background: var(--ink); }
</style>
</head>
<body>
<main class="sheet">
  <section class="card card-back" aria-label="Business card, contact side">
    <div class="brand-mark">Cedar Ridge Mechanical</div>
    <p class="address">Your address, City<br>State, Zip 1234</p>
    <div class="company"><span class="square"></span>Cedar Ridge Mechanical</div>
    <div class="person">
      <p class="name">Daniel Hart</p>
      <p class="role">Managing Director</p>
    </div>
    <ul class="contacts">
      <li>123 456 789
        <svg viewBox="0 0 24 24" aria-hidden="true"><path d="M6.6 10.8a15 15 0 0 0 6.6 6.6l2.2-2.2a1 1 0 0 1 1-.25 11.4 11.4 0 0 0 3.6.6 1 1 0 0 1 1 1V20a1 1 0 0 1-1 1A17 17 0 0 1 3 4a1 1 0 0 1 1-1h3.5a1 1 0 0 1 1 1c0 1.25.2 2.45.6 3.6a1 1 0 0 1-.25 1z"/></svg></li>
      <li>info@yourmail.com
        <svg viewBox="0 0 24 24" aria-hidden="true"><path d="M2 5h20v14H2zm2 2v.5l8 5 8-5V7zm0 2.8V17h16V9.8l-8 5z"/></svg></li>
      <li>www.yourwebsite.com
        <svg viewBox="0 0 24 24" aria-hidden="true"><path d="M12 2a10 10 0 1 0 0 20 10 10 0 0 0 0-20zm6.9 6h-3a15 15 0 0 0-1.3-3.7A8 8 0 0 1 18.9 8zM12 4c.8 1.2 1.5 2.5 1.9 4h-3.8c.4-1.5 1.1-2.8 1.9-4zM4.3 14a8 8 0 0 1 0-4h3.4a16 16 0 0 0 0 4zm.8 2h3a15 15 0 0 0 1.3 3.7A8 8 0 0 1 5.1 16zm3-8h-3a8 8 0 0 1 4.3-3.7A15 15 0 0 0 8.1 8zM12 20c-.8-1.2-1.5-2.5-1.9-4h3.8c-.4 1.5-1.1 2.8-1.9 4zm2.3-6H9.7a14 14 0 0 1 0-4h4.6a14 14 0 0 1 0 4zm.3 5.7a15 15 0 0 0 1.3-3.7h3a8 8 0 0 1-4.3 3.7zm1.7-5.7a16 16 0 0 0 0-4h3.4a8 8 0 0 1 0 4z"/></svg></li>
    </ul>
    <div class="edge-strip"></div>
  </section>

  <section class="card card-front" aria-label="Business card, brand side">
    <div class="company"><span class="square"></span>Cedar Ridge Mechanical</div>
  </section>
</main>
</body>
</html>
```